Australian Trucking Company Requires Professional Looking Stationary

We require a professional looking stationary design that incorporates our newly designed logo.

Our business, called "Brell Haulage Contracting", provides contracting work, transport and logistics to business in Western Australia particularly with links to the mining sector.

We are a small business looking to expand and our new logo and our new stationary will help develop our brand image in our market place.

Target Market(s)

Businesses and Corporation with links to the Mining Sector

Industry/Entity Type

Small Business

Requirements
Must have
• The letterhead must have the following details:
The new logo

Text saying: "Brell Holdings Pty Ltd (ACN 582 316 907) ATF The Brell Discretionary Trust T/AS"
"ABN 71 834 209 553"
Address "P.O Box 817 Wattlegrove WA, 6958"
Phone: 08 9352 7140
Email: brellhaul@mailbox-example.com.au

The text on the letterhead should be editable as the details are likely to change in the near future. Provision should be made for a website address all though one isn't available at the moment.

The styling, layout and font text is entirely up to the designer.

```html
<!DOCTYPE html>
<html lang="en">
<head>
<meta charset="utf-8">
<title>Brell Haulage Contracting – Business Card</title>
<link rel="stylesheet" href="https://fonts.googleapis.com/css2?family=Source+Sans+3:wght@400;600;700&display=swap">
<style>
  :root {
    --backdrop: #ece9e6;
    --card: #ffffff;
    --brand-red: #c4161c;
    --brand-red-dark: #8e0f13;
    --swoosh-grey: #b9b9b9;
    --ink: #222222;
    --rule: #d6d6d6;
  }
  * { box-sizing: border-box; margin: 0; padding: 0; }
  html, body {
    width: 1200px; height: 426px; overflow: hidden;
    background: var(--backdrop);
    font-family: "Source Sans 3", Arial, sans-serif;
    color: var(--ink);
  }
  .card {
    position: absolute; top: 57px;
    width: 516px; height: 297px;
    background: var(--card);
    border-radius: 18px;
    overflow: hidden;
    box-shadow: 0 2px 6px rgba(0,0,0,.15);
  }
  .card--front { left: 70px; }
  .card--back { left: 615px; }

  .front-header { position: absolute; left: 0; top: 0; width: 516px; height: 60px; }
  .holder {
    position: absolute; top: 13px; left: 0; width: 100%;
    text-align: center; color: #fff;
    font-weight: 700; font-size: 19px;
  }
  .holder-role { font-weight: 400; font-size: 13px; }

  .brand-name {
    position: absolute; left: 96px; top: 92px; width: 360px;
    color: var(--brand-red);
    font-weight: 700; font-size: 36px; line-height: 38px;
    text-transform: uppercase; letter-spacing: .5px;
  }
  .brand-mark {
    position: absolute; left: 70px; top: 100px;
    width: 16px; height: 16px; background: var(--brand-red);
  }

  .contact {
    position: absolute; left: 0; width: 100%;
    text-align: center; font-size: 13px; line-height: 16px;
  }
  .contact svg { width: 11px; height: 11px; vertical-align: -1px; margin-right: 3px; fill: var(--brand-red); }
  .contact-line--top { top: 206px; }
  .contact-line--top span + span { margin-left: 8px; }
  .contact-line--address { top: 226px; }
  .divider {
    position: absolute; left: 70px; right: 70px; top: 249px;
    border-top: 1px solid var(--rule);
  }
  .legal { position: absolute; left: 0; width: 100%; text-align: center; font-size: 12px; line-height: 16px; }
  .legal--entity { top: 258px; }
  .legal--abn { top: 277px; }

  .back-name {
    position: absolute; left: 0; top: 118px; width: 100%;
    text-align: center; color: var(--brand-red);
    font-weight: 700; font-size: 30px; text-transform: uppercase;
  }
</style>
</head>
<body>

<section class="card card--front">
  <svg class="front-header" viewBox="0 0 516 60" aria-hidden="true">
    <defs>
      <linearGradient id="headerRed" x1="0" y1="0" x2="0" y2="1">
        <stop offset="0" stop-color="#9c1016"/>
        <stop offset="1" stop-color="#d21e24"/>
      </linearGradient>
    </defs>
    <path d="M0 46 Q258 30 516 46 L516 52 Q258 37 0 56 Z" fill="var(--swoosh-grey)"/>
    <path d="M0 0 H516 V40 Q258 28 0 46 Z" fill="url(#headerRed)"/>
  </svg>
  <p class="holder">Persons name, <span class="holder-role">Manager</span></p>

  <span class="brand-mark"></span>
  <p class="brand-name">Brell Haulage<br>Contracting</p>

  <p class="contact contact-line--top">
    <span><svg viewBox="0 0 24 24"><path d="M6.6 10.8a15.1 15.1 0 0 0 6.6 6.6l2.2-2.2a1 1 0 0 1 1-.25 11.4 11.4 0 0 0 3.6.57 1 1 0 0 1 1 1V20a1 1 0 0 1-1 1A17 17 0 0 1 3 4a1 1 0 0 1 1-1h3.5a1 1 0 0 1 1 1c0 1.25.2 2.45.57 3.57a1 1 0 0 1-.25 1z"/></svg>08 9352 7140</span>
    <span><svg viewBox="0 0 24 24"><path d="M2 5h20v14H2z M4 7v.5l8 5 8-5V7z" fill-rule="evenodd"/></svg>brellhaul@mailbox-example.com.au</span>
  </p>
  <p class="contact contact-line--address">
    <svg viewBox="0 0 24 24"><path d="M12 3 2 12h3v8h5v-5h4v5h5v-8h3z"/></svg>P.O Box 817 Wattlegrove WA, 6958
  </p>
  <div class="divider"></div>
  <p class="legal legal--entity">Brell Holdings Pty Ltd (ACN 582 316 907) ATF The Brell Discretionary Trust T/AS</p>
  <p class="legal legal--abn">ABN 71 834 209 553</p>
</section>

<section class="card card--back">
  <p class="back-name">Brell Haulage<br>Contracting</p>
</section>

</body>
</html>
```